HOT TUB - SPAS service needs an business card

I need an business for my company who his specialise in a maintenance,water treatment and cleaning of Hot Tub - Spas for commercial and residential customers. The company operate mainly in the ski resort of Chamonix, Megève and St Gervais. The final product should communicate pure water, cleanest and professional for luxury property's.
I have upload a logo but any improvement on it is welcome.(color,size, details etc..) or any other idea. Thank you
Company Name: 58 BAINS
My name: Lucien Marchetti
Email: lucimarch@examplemail.net
Tel: +33 (0)6 71 58 29 64
Description to be on the card in french(first langage) and in English:
- Spas service
- Entretien, traitement eau, nettoyage.
- Maintenance, water treatment, cleaning.
Industry/Entity Type
Residential
Colors
Designer to choose colors to be used in the design.
Look and feel
Each slider illustrates characteristics of the customer's brand and the style your logo design should communicate.

```html
<!DOCTYPE html>
<html lang="fr">
<head>
<meta charset="utf-8">
<title>58 BAINS – Cartes de visite</title>
<link rel="stylesheet" href="https://fonts.googleapis.com/css2?family=Source+Sans+3:wght@400;600;700&display=swap">
<style>
  :root {
    --page-bg: #eef1f4;
    --water-light: #3db2f2;
    --water-mid: #2a9ce8;
    --water-deep: #1e88dc;
    --band-deep: #1563c6;
    --band-edge: #8fd0f8;
    --ink-white: #ffffff;
  }
  * { box-sizing: border-box; margin: 0; padding: 0; }
  html, body {
    width: 1200px;
    height: 1003px;
    overflow: hidden;
    background: var(--page-bg);
    font-family: "Source Sans 3", "Myriad Pro", sans-serif;
    color: var(--ink-white);
  }
  .canvas { position: relative; width: 1200px; height: 1003px; }

  .card {
    position: absolute;
    width: 784px;
    height: 447px;
    border-radius: 36px;
    overflow: hidden;
  }
  .card--front { left: 389px; top: 38px; }
  .card--back  { left: 46px;  top: 532px; }

  .card__water {
    position: absolute;
    inset: 0;
    background:
      radial-gradient(ellipse at 30% 25%, var(--water-light) 0%, transparent 60%),
      linear-gradient(160deg, var(--water-light) 0%, var(--water-mid) 50%, var(--water-deep) 100%);
  }

  .brand-mark {
    position: absolute;
    display: flex;
    align-items: center;
    justify-content: center;
    gap: 16px;
    font-weight: 600;
    letter-spacing: 1px;
  }
  .brand-mark__dot {
    width: 22px; height: 22px;
    border: 2px solid var(--ink-white);
    border-radius: 50%;
  }
  .card--front .brand-mark { left: 147px; top: 41px; width: 501px; height: 138px; font-size: 34px; }
  .card--back  .brand-mark { left: 97px;  top: 85px; width: 603px; height: 168px; font-size: 40px; }

  .company-name {
    position: absolute;
    left: 0; right: 0;
    top: 220px;
    text-align: center;
    font-size: 37px;
    font-weight: 600;
  }

  .contact-band { position: absolute; inset: 0; }

  .contact {
    position: absolute;
    left: 0; right: 0;
    top: 318px;
    text-align: center;
  }
  .contact__name { font-size: 27px; font-weight: 700; line-height: 38px; }
  .contact__line {
    display: flex; align-items: center; justify-content: center; gap: 8px;
    font-size: 25px; font-weight: 400; line-height: 42px;
  }
  .contact__icon { width: 22px; height: 22px; }

  .services {
    position: absolute;
    left: 0; right: 0;
    top: 308px;
    text-align: center;
  }
  .services__title { font-size: 27px; font-weight: 600; line-height: 42px; margin-left: -10px; }
  .services__list {
    list-style: none;
    display: flex; justify-content: center; gap: 14px;
    font-size: 27px; line-height: 38px;
    margin-left: -40px;
  }
  .services__list li::before { content: "• "; }
</style>
</head>
<body>
<main class="canvas">

  <section class="card card--front" aria-label="Recto de la carte">
    <div class="card__water" role="img" aria-label="Fond de gouttes d'eau sur surface bleue"></div>
    <div class="brand-mark"><span class="brand-mark__dot"></span>58 BAINS</div>
    <h1 class="company-name">58 BAINS</h1>
    <svg class="contact-band" viewBox="0 0 784 447" preserveAspectRatio="none" aria-hidden="true">
      <path d="M0,380 Q392,212 784,385 L784,447 L0,447 Z" fill="var(--band-deep)"/>
      <path d="M0,372 Q392,204 784,377" fill="none" stroke="var(--band-edge)" stroke-width="4" opacity="0.85"/>
    </svg>
    <div class="contact">
      <p class="contact__name">Lucien Marchetti</p>
      <p class="contact__line">
        <svg class="contact__icon" viewBox="0 0 24 24" aria-hidden="true">
          <circle cx="12" cy="12" r="10" fill="none" stroke="#fff" stroke-width="1.6"/>
          <path d="M9 6.5c-1.5 1-2 3-1 5.5s3 4.5 5 5.5c1 .5 2 .3 2.6-.5l-2-2-1.2.8c-1.3-.8-2.4-2-3-3.4l1-1-1.4-2.6z" fill="#fff"/>
        </svg>
        +33 (0)6 71 58 29 64
      </p>
      <p class="contact__line">
        <svg class="contact__icon" viewBox="0 0 24 24" aria-hidden="true">
          <path d="M2 10 L12 4 L22 10 V20 H2 Z" fill="#fff"/>
          <path d="M2 10 L12 16 L22 10" fill="none" stroke="var(--band-deep)" stroke-width="1.6"/>
        </svg>
        lucimarch@examplemail.net
      </p>
    </div>
  </section>

  <section class="card card--back" aria-label="Verso de la carte">
    <div class="card__water" role="img" aria-label="Fond de gouttes d'eau sur surface bleue"></div>
    <div class="brand-mark"><span class="brand-mark__dot"></span>58 BAINS</div>
    <div class="services">
      <h2 class="services__title">SPAS SERVICES</h2>
      <ul class="services__list" lang="fr">
        <li>Entretien</li><li>traitement eau</li><li>nettoyage</li>
      </ul>
      <ul class="services__list" lang="en">
        <li>Maintenance</li><li>water treatment</li><li>cleaning.</li>
      </ul>
    </div>
  </section>

</main>
</body>
</html>
```